Tusk Hollow Lodge website (design only)

Tusk Hollow Lodge (http://www.tuskhollowlodge-mw.example) is a private Safari lodge located in Malawi.
We would like a modern, professional website designed that does not subscribe to the cliched view of a Safari in Africa, but still maintain a wildlife/safari atmosphere.

The aim of our website is to entice people & drive them to the booking form.

Here are some examples of websites that we like. Although we would like our site to be a bit more in line with modern web design trends.

http://www.marulaplains.example/
http://www.kovunde.example/
http://www.tembalorecamp.example/

Requirements
Must have
• Here is a list of the pages required. Most of them will follow a standard content layout. I.e. heading, body and images.

If you take a look at the website, you will get an idea of hoe many page types there are +- 5

http://www.tuskhollowlodge-mw.example/index.htm

About Tusk Hollow
Lirundu Country Club
Rooms
Conferences
Cuisine
Facilities
Your Safari
Activities
Rates & Special Offers
Booking form
Latest Developments
How To Get There
Gallery
Contact Us
Blog / Newsfeed

```html
<!DOCTYPE html>
<html lang="en">
<head>
<meta charset="utf-8">
<title>Tusk Hollow Lodge</title>
<link rel="stylesheet" href="https://fonts.googleapis.com/css2?family=Federo&family=Gabriela&family=Ubuntu:wght@400;500&display=swap">
<style>
  :root {
    --page-bg: #161616;
    --panel-bg: #1e1e1e;
    --orange: #f5a21f;
    --orange-light: #fbbd4a;
    --orange-dark: #e28f0c;
    --heading: #f4a62a;
    --text: #f2f2f2;
    --muted: #b9b9b9;
    --thumb-border: #7a7a7a;
    --button-text: #2a1a05;
  }
  * { box-sizing: border-box; margin: 0; padding: 0; }
  html, body { width: 942px; height: 1200px; overflow: hidden; }
  body {
    position: relative;
    background: var(--page-bg);
    font-family: "Ubuntu", sans-serif;
    color: var(--text);
  }
  .hero {
    position: absolute; left: 0; top: 0; width: 942px; height: 421px;
    background:
      linear-gradient(180deg, rgba(0,0,0,0) 55%, rgba(20,30,20,.35) 100%),
      linear-gradient(90deg, #6e5a3c 0%, #8a6d45 25%, #3f6173 42%, #2d5fa8 60%, #3a78c0 100%);
  }
  .hero-landscape {
    position: absolute; left: 0; top: 250px; width: 942px; height: 171px;
    background: linear-gradient(180deg, #5f7f72 0%, #6f8f3a 40%, #4f7a23 100%);
  }
  .top-links {
    position: absolute; top: 12px; right: 72px;
    display: flex; gap: 14px; list-style: none; font-size: 10.5px;
  }
  .top-links li::before { content: "●"; font-size: 7px; margin-right: 5px; color: #111; vertical-align: 1px; }
  .brand {
    position: absolute; left: 31px; top: 84px;
    font-family: "Federo", sans-serif; font-size: 44px; letter-spacing: 1px;
    color: var(--orange);
  }
  .main-nav {
    position: absolute; left: 18px; top: 421px; width: 904px; height: 35px;
    display: flex; list-style: none;
    background: linear-gradient(180deg, var(--orange-light), var(--orange-dark));
    font-family: "Gabriela", serif; font-size: 12.5px; color: #2b1a06;
  }
  .main-nav li {
    display: flex; align-items: center; padding: 0 9px;
    border-right: 1px solid rgba(120,70,0,.45);
  }
  .main-nav li:last-child { border-right: 0; }
  .content {
    position: absolute; left: 18px; top: 456px; width: 904px; height: 653px;
    background: var(--panel-bg);
  }
  .block { position: absolute; }
  .thumb {
    display: block; width: 259px; height: 122px;
    border: 2px solid var(--thumb-border);
  }
  .section-title {
    font-family: "Gabriela", serif; font-weight: 400;
    color: var(--heading); font-size: 19px;
  }
  .copy {
    font-size: 12.5px; line-height: 17.5px; text-align: justify;
  }
  .button {
    position: absolute; display: flex; align-items: center; justify-content: center;
    height: 27px; border-radius: 4px; font-size: 12px;
    background: linear-gradient(180deg, var(--orange-light), var(--orange));
    color: var(--button-text);
  }
  .card { width: 259px; }
  .card .section-title { margin-top: 12px; margin-bottom: 10px; }
  .updates { left: 615px; top: 26px; width: 259px; }
  .updates h3 { font-weight: 400; font-size: 14.5px; color: var(--muted); margin: 10px 0 8px; letter-spacing: .3px; }
  .updates .copy { font-size: 11.5px; text-align: left; }
  .updates .copy + h3 { margin-top: 24px; }
  .welcome { left: 27px; top: 393px; width: 422px; }
  .welcome .copy { margin-top: 16px; }
  .welcome .copy + .copy { margin-top: 17px; }
  .gallery-title { left: 488px; top: 393px; }
  .gallery-thumb { position: absolute; top: 441px; width: 151px; height: 126px; border: 2px solid var(--thumb-border); }
  .arrow { position: absolute; top: 493px; }
  .footer-links {
    position: absolute; top: 1128px; left: 0; width: 942px;
    display: flex; justify-content: center; gap: 12px; list-style: none;
    font-size: 10.5px; color: #b5b5b5;
  }
  .footer-links li::before { content: "●"; font-size: 6px; margin-right: 4px; color: #555; vertical-align: 2px; }
  .footer-rule { position: absolute; top: 1155px; left: 18px; width: 904px; height: 1px; background: #2e2e2e; }
  .legal {
    position: absolute; top: 1172px; left: 0; width: 942px;
    text-align: center; font-size: 9.5px; color: #9a9a9a;
  }
</style>
</head>
<body>
  <header class="hero">
    <div class="hero-landscape" role="img" aria-label="Thatched lodge with open dining room beside an infinity pool, overlooking green bushland under a blue evening sky with the moon"></div>
    <ul class="top-links">
      <li>About Tusk Hollow</li>
      <li>Our Blog</li>
      <li>Contact Us</li>
    </ul>
    <div class="brand">Tusk Hollow Lodge</div>
  </header>

  <ul class="main-nav">
    <li>Rooms</li><li>Conferences</li><li>Cuisine</li><li>Facilities</li><li>Your Safari</li><li>Activities</li><li>Rates &amp; Special Offers</li><li>Booking requests</li><li>Latest Developments</li><li>How To Get There</li><li>Gallery</li>
  </ul>

  <main class="content">
    <section class="block card" style="left:27px; top:28px;">
      <div class="thumb" role="img" aria-label="Outdoor lounge deck with sofas and a fire pit at sunset" style="background:linear-gradient(180deg,#6b6a78 0%,#8a6a55 50%,#3a2c22 100%);"></div>
      <h2 class="section-title">Facilities</h2>
      <p class="copy">Lorem Ipsum is simply dummy text of the printing and typesetting industry. Lorem Ipsum has been the industry's standard dummy text ever since the 1500s, when an unknown printer took a galley of type and scrambled it to make a type specimen book.</p>
    </section>
    <a class="button" style="left:207px; top:326px; width:76px;">read more</a>

    <section class="block card" style="left:321px; top:28px;">
      <div class="thumb" role="img" aria-label="Safari vehicle on a grassy plain below a green hillside" style="background:linear-gradient(180deg,#7fb0d8 0%,#4f7a3a 35%,#3f6a2e 65%,#b8a060 100%);"></div>
      <h2 class="section-title">Your Safari</h2>
      <p class="copy">Lorem Ipsum is simply dummy text of the printing and typesetting industry. Lorem Ipsum has been the industry's standard dummy text ever since the 1500s, when an unknown printer took a galley of type and scrambled it to make a type specimen book.</p>
    </section>
    <a class="button" style="left:504px; top:326px; width:76px;">read more</a>

    <section class="block updates">
      <h2 class="section-title">Tusk Hollow Updates</h2>
      <h3>Project Development</h3>
      <p class="copy">The 2nd phase commenced in February 2011 and consists of:-<br>Construction of an international&nbsp; 18 hole golf course by Dravenko &amp; Pell, renowned golf course designers from South Africa....</p>
      <h3>Safari</h3>
      <p class="copy" style="text-align:justify;">We have supplemented our game park with indigenous Malawi wild life which consists of sable, waterbuck, zebra, impala, wildebeest, nyala, giraffe and&nbsp; numerous duiker and smaller wild cats and otters.....</p>
    </section>
    <a class="button" style="left:798px; top:326px; width:76px;">read more</a>

    <section class="block welcome">
      <h2 class="section-title">Welcome to Tusk Hollow</h2>
      <p class="copy" style="text-align:left;">Warmest welcome to the unique Malawi experience. lodge complex, game park, the 18 hole Lirundu golf club and Lusewa dam.</p>
      <p class="copy">A multi million&nbsp; dollar development at Kalembo estate, Mkanda on Mtendere road 20 kms from Blantyre Malawi's commercial capital creating a fascinating paradise&nbsp; for multiple leisure activities and conserving Malawi wildlife.Our Lodge also has beautifully designed and built&nbsp; in golden colored rock.</p>
    </section>
    <a class="button" style="left:371px; top:581px; width:76px;">read more</a>

    <h2 class="block section-title gallery-title">Gallery</h2>
    <svg class="arrow" style="left:491px;" width="14" height="24" viewBox="0 0 14 24" aria-hidden="true"><path d="M11 2 L3 12 L11 22" fill="none" stroke="#9a9a9a" stroke-width="3"/></svg>
    <div class="gallery-thumb" style="left:519px; background:linear-gradient(135deg,#7a8a3a 0%,#4a4238 50%,#6a7a30 100%);" role="img" aria-label="Waterbuck standing in grassland"></div>
    <div class="gallery-thumb" style="left:688px; background:linear-gradient(180deg,#8a9aa0 0%,#5a3a2a 40%,#6a6a50 75%,#4a5a40 100%);" role="img" aria-label="Wooden cabin with chairs around an evening fire pit"></div>
    <svg class="arrow" style="left:853px;" width="14" height="24" viewBox="0 0 14 24" aria-hidden="true"><path d="M3 2 L11 12 L3 22" fill="none" stroke="#9a9a9a" stroke-width="3"/></svg>
    <a class="button" style="left:783px; top:581px; width:76px;">view all</a>
  </main>

  <ul class="footer-links">
    <li>About Tusk Hollow</li>
    <li>Our Blog</li>
    <li>Contact Us</li>
  </ul>
  <div class="footer-rule"></div>
  <p class="legal">2012 © www.tuskhollowlodge-mw.example | All rights reserved | Terms of Service - Privacy Policy - Program Policies</p>
</body>
</html>
```